We are a recruitment company based in Norwich/Cambridge England.
I have included our company logo which we want to remain the same.

What we are looking for is a new creative Business card which will really stand out!!

Contact Information for Business Card

Harriet Dunmore
email: Harriet@plavex.co.uk
Address: Brackwell House
Fenmoor Enterprise Park
Partridge Way
Norwich
QB9 3KX
Tel:01632 960418

```html
<!DOCTYPE html>
<html lang="en">
<head>
<meta charset="utf-8">
<title>Plavex – Business Card</title>
<link rel="stylesheet" href="https://fonts.googleapis.com/css2?family=Montserrat:wght@600;700&family=Roboto:wght@400&display=swap">
<style>
  :root{
    --backdrop:#2b2b2b;
    --paper:#f1f1f1;
    --green:#8cc43f;
    --grey:#8e898f;
    --grey-dark:#7c777e;
    --white:#ffffff;
  }
  *{margin:0;padding:0;box-sizing:border-box}
  html,body{width:1200px;height:960px;overflow:hidden;background:var(--backdrop)}
  .canvas{position:relative;width:1200px;height:960px}
  .card{position:absolute;width:600px;height:342px;overflow:hidden}
  .card-front{left:322px;top:108px;background:var(--paper)}
  .card-back{left:320px;top:493px;background:var(--grey)}
  .wave{position:absolute;left:0;top:0}

  .brand{position:absolute;left:48px;top:44px;display:flex;align-items:center;gap:12px}
  .brand-dot{width:46px;height:46px;border-radius:50%;background:var(--green)}
  .brand-name{font-family:'Montserrat',sans-serif;font-weight:600;font-size:42px;color:var(--grey);line-height:1}
  .brand-tagline{position:absolute;left:156px;top:107px;font-family:'Roboto',sans-serif;font-size:8.5px;letter-spacing:1.3px;color:var(--grey)}

  .person{position:absolute;right:22px;top:190px;text-align:right;color:var(--white);font-family:'Montserrat',sans-serif;font-weight:700}
  .person-name{font-size:20px;line-height:24px}
  .person-role{font-size:15px;line-height:20px}

  .address{position:absolute;right:197px;top:270px;text-align:right;color:var(--white);font-family:'Roboto',sans-serif;font-size:14px;line-height:20px}
  .web{letter-spacing:2.6px}
  .divider{position:absolute;left:414px;top:255px;width:1px;height:72px;background:rgba(255,255,255,.7)}

  .contacts{position:absolute;right:22px;top:248px;list-style:none;color:var(--white);font-family:'Roboto',sans-serif;font-size:14px;line-height:19.5px}
  .contacts li{display:flex;justify-content:flex-end;align-items:center;gap:8px}
  .contacts svg{width:13px;height:13px;fill:var(--white)}

  .back-brand{position:absolute;left:0;right:0;top:118px;display:flex;justify-content:center;align-items:center;gap:16px}
  .back-dot{width:60px;height:60px;border-radius:50%;background:var(--white)}
  .back-name{font-family:'Montserrat',sans-serif;font-weight:600;font-size:60px;color:var(--white);line-height:1}
  .back-web{position:absolute;left:0;right:0;top:300px;text-align:center;color:var(--white);font-family:'Roboto',sans-serif;font-size:14px;letter-spacing:4.5px}
</style>
</head>
<body>
<main class="canvas">
  <section class="card card-front">
    <svg class="wave" width="600" height="342" viewBox="0 0 600 342" aria-hidden="true">
      <path fill="var(--grey-dark)" d="M178,342 C192,250 255,182 335,182 L392,185 C410,104 492,56 600,56 L600,342 Z"/>
      <path fill="var(--green)" d="M195,342 C210,252 272,186 350,186 L403,188 C422,112 502,64 600,64 L600,342 Z"/>
    </svg>

    <div class="brand">
      <span class="brand-dot"></span>
      <span class="brand-name">Plavex</span>
    </div>
    <div class="brand-tagline">Technology Recruitment</div>

    <div class="person">
      <div class="person-name">HARRIET DUNMORE</div>
      <div class="person-role">CEO/FOUNDER</div>
    </div>

    <div class="address">
      <div>Brackwell House</div>
      <div>Norwich QB9 3KX</div>
      <div class="web">www.plavex.co.uk</div>
    </div>
    <span class="divider"></span>

    <ul class="contacts">
      <li>01632 960418
        <svg viewBox="0 0 24 24"><path d="M6.6 10.8a15.1 15.1 0 0 0 6.6 6.6l2.2-2.2c.3-.3.7-.4 1-.2 1.1.4 2.3.6 3.6.6.6 0 1 .4 1 1V20c0 .6-.4 1-1 1A17 17 0 0 1 3 4c0-.6.4-1 1-1h3.5c.6 0 1 .4 1 1 0 1.3.2 2.5.6 3.6.1.3 0 .7-.2 1z"/></svg></li>
      <li>07700 900264
        <svg viewBox="0 0 24 24"><path d="M7 1h10a2 2 0 0 1 2 2v18a2 2 0 0 1-2 2H7a2 2 0 0 1-2-2V3a2 2 0 0 1 2-2zm0 3v14h10V4zm5 15.5a1 1 0 1 0 0 2 1 1 0 0 0 0-2z"/></svg></li>
      <li>01632 960733
        <svg viewBox="0 0 24 24"><path d="M6 2h12v6H6zM3 9h18a2 2 0 0 1 2 2v7h-4v4H5v-4H1v-7a2 2 0 0 1 2-2zm4 8v3h10v-3z"/></svg></li>
      <li>Harriet@plavex.co.uk
        <svg viewBox="0 0 24 24"><path d="M2 5h20v14H2zm2 2v.5l8 5 8-5V7z"/></svg></li>
    </ul>
  </section>

  <section class="card card-back">
    <div class="back-brand">
      <span class="back-dot"></span>
      <span class="back-name">Plavex</span>
    </div>
    <div class="back-web">www.plavex.co.uk</div>
  </section>
</main>
</body>
</html>
```